Business card for acupunctist in Melbourne. Specialises in Fertility, pre and post natal care, pain

I am looking for a business card which is going to catch people eyes. Two sided, one side in a muted colour (keeping it feminine) (pink or yellow???)maybe with a little simple logo or picture, the other side I was thinking white with 3 colours (pink grey and yellow... Had these in mind.
Info on the card
Mirren Costa Acupuncture

Dr Mirren Costa (TCM Acupuncture)
Acupuncture for balancing body and mind.
Willowmere Therapeutics
14 Ferndale Road, Oakhurst 3071.
94726151
0428319574
Mirrentcm@quillpost.net

Some other little logo/ designs I have liked are as follows:
http://www.dorotheabrisklac.net/rates-and-insurance/
http://www.rosalindpeverell.net/
http://www.tz-acupuncture.example.uk/

Target Market(s)

professional women, people in pain, active people, people seeking a healthy lifefstyle.

Industry/Entity Type

Business

Font styles to use
Serif
Sans Serif

Colors
eea4c8
fde08a
aaaaaa

Requirements
Must have
• Must be eye catching, but not too loud and busy. Subltle is good. Simple is also good. The logo could be something that represents growth and health and nurturing. Again not too elaborate, very simple.
Thankyou
Should not have
• Electric colours, crazy fonts, Pictures of yin and yang, candles, or bodies.

```html
<!DOCTYPE html>
<html lang="en">
<head>
<meta charset="utf-8">
<title>Mirren Costa Acupuncture – Business Card</title>
<link rel="stylesheet" href="https://fonts.googleapis.com/css2?family=Open+Sans:wght@400;600;700&display=swap">
<style>
  :root {
    --pink: #e79ccb;
    --pink-soft: #eea4c8;
    --yellow: #f1de85;
    --grey: #aaaaaa;
    --ink: #2b2b2b;
    --paper: #ffffff;
    --backdrop: #e9e9e9;
  }
  * { box-sizing: border-box; margin: 0; padding: 0; }
  html, body {
    width: 1200px; height: 1200px; overflow: hidden;
    background: var(--backdrop);
    font-family: "Open Sans", Arial, sans-serif;
  }
  .sheet {
    width: 1200px; height: 1200px;
    display: flex; flex-direction: column; align-items: center; justify-content: center;
    gap: 60px;
  }
  .card {
    position: relative;
    width: 800px; height: 489px;
    background: var(--paper);
    overflow: hidden;
    box-shadow: 0 6px 18px rgba(0,0,0,0.12);
  }

  /* Brand name block (stands where the mark sits) */
  .brand {
    position: absolute;
    display: flex; align-items: center; gap: 16px;
  }
  .brand-dot {
    width: 46px; height: 46px; border-radius: 50%;
    background: var(--pink-soft);
    flex: none;
  }
  .brand-name {
    color: var(--pink);
    font-weight: 400;
    line-height: 1.05;
  }

  /* Front */
  .front-block-yellow {
    position: absolute; left: 0; top: 98px;
    width: 250px; height: 150px;
    background: var(--yellow);
  }
  .front-block-pink {
    position: absolute; right: 0; top: 320px;
    width: 120px; height: 120px;
    background: var(--pink);
  }
  .front .brand { left: 300px; top: 196px; }
  .front .brand-name { font-size: 34px; }

  /* Back */
  .back .brand { right: 60px; top: 70px; }
  .back .brand-name { font-size: 28px; }
  .band-pink {
    position: absolute; left: 0; right: 0; top: 200px; height: 105px;
    background: var(--pink);
  }
  .band-yellow {
    position: absolute; left: 0; right: 0; top: 305px; bottom: 0;
    background: var(--yellow);
  }
  .identity {
    position: absolute; left: 150px; top: 214px;
    color: var(--ink);
  }
  .identity-name { font-size: 27px; font-weight: 700; }
  .identity-name .credential { font-size: 18px; font-weight: 400; }
  .identity-line { font-size: 18px; line-height: 1.35; }
  .address {
    position: absolute; left: 70px; top: 335px;
    font-size: 20px; line-height: 1.35; color: var(--ink);
  }
  .contacts {
    position: absolute; left: 410px; top: 335px;
    list-style: none;
    font-size: 21px; color: var(--ink);
  }
  .contacts li { display: flex; align-items: center; gap: 12px; margin-bottom: 8px; }
  .contact-icon {
    width: 22px; height: 22px; flex: none;
  }
</style>
</head>
<body>
<main class="sheet">

  <section class="card front" aria-label="Business card front">
    <div class="front-block-yellow"></div>
    <div class="brand">
      <span class="brand-dot"></span>
      <span class="brand-name">Mirren Costa<br>Acupuncture</span>
    </div>
    <div class="front-block-pink"></div>
  </section>

  <section class="card back" aria-label="Business card back">
    <div class="brand">
      <span class="brand-dot"></span>
      <span class="brand-name">Mirren Costa<br>Acupuncture</span>
    </div>
    <div class="band-pink"></div>
    <div class="band-yellow"></div>

    <div class="identity">
      <p class="identity-name">Dr Mirren Costa <span class="credential">(TCM Acupuncture)</span></p>
      <p class="identity-line">Acupuncture for balancing body and mind.</p>
      <p class="identity-line">Willowmere Therapeutics</p>
    </div>

    <address class="address" style="font-style:normal">
      14 Ferndale Road,<br>Oakhurst 3071.
    </address>

    <ul class="contacts">
      <li>
        <svg class="contact-icon" viewBox="0 0 22 22" aria-hidden="true">
          <rect width="22" height="22" rx="5" fill="#e79ccb"/>
          <path d="M7 5.5c1 0 1.6 2.6 1.2 3.2l-1 .9c.7 1.6 2 2.9 3.6 3.6l.9-1c.6-.4 3.2.2 3.2 1.2v1.6c0 .6-.5 1-1.1 1C9.2 16 6 12.8 6 8.2 6 6 6.4 5.5 7 5.5z" fill="#fff"/>
        </svg>
        94726151
      </li>
      <li>
        <svg class="contact-icon" viewBox="0 0 22 22" aria-hidden="true">
          <rect width="22" height="22" rx="5" fill="#e79ccb"/>
          <rect x="7.5" y="4.5" width="7" height="13" rx="1.5" fill="#fff"/>
          <circle cx="11" cy="15.3" r="0.9" fill="#e79ccb"/>
        </svg>
        0428319574
      </li>
      <li>
        <svg class="contact-icon" viewBox="0 0 22 22" aria-hidden="true">
          <rect width="22" height="22" rx="5" fill="#e79ccb"/>
          <rect x="5" y="7" width="12" height="8.5" rx="1" fill="#fff"/>
          <path d="M5.5 7.5 11 12l5.5-4.5" fill="none" stroke="#e79ccb" stroke-width="1.2"/>
        </svg>
        Mirrentcm@quillpost.net
      </li>
    </ul>
  </section>

</main>
</body>
</html>
```